Detail Shop Business card design

i need a business card design for my new detailing company called 'Brisk's Polish Works'. i want an all black and white design . simple, direct and to the point. i want the designer to choose a fitting font to match the logothe front should have logo, address, phone and email and the back side should have a slogan and text indicating that we offer services on anything including cars, trucks, motorcycles and RVs. slogan will read "we take pride in your ride"
maybe also very small on the back side the IG icon with Brisks_Polish_Works

phone 208.417.6352
address 3847 E Larkin Ave
Spokane WA 99214
email: BrisksPolish@mailvexo.com

Target Market(s)

all ages , auto enthusiasts

Industry/Entity Type

Automotive

Contact Information for Business Card

the front should have logo, address, phone and email and the back side should have a slogan and text indicating that we offer services on anything including cars, trucks, motorcycles and RVs. slogan will read "we take pride in your ride"

phone 208.417.6352
address 3847 E Larkin Ave
Spokane WA 99214

Colors
000000
ffffff

Requirements
Must have
• bold font and very simple design with good spacing
Nice to have
• anything creative from the designer indicating we service any types of vehicles
Should not have
• any colors ,

```html
<!DOCTYPE html>
<html lang="en">
<head>
<meta charset="utf-8">
<title>Brisk's Polish Works – Business Card</title>
<link rel="stylesheet" href="https://fonts.googleapis.com/css2?family=Roboto:wght@400;500;700&family=Roboto+Condensed:wght@400;700&display=swap">
<style>
  :root {
    --ink: #000000;
    --paper: #ffffff;
    --paper-soft: #f2f2f2;
    --backdrop: #2a2a2a;
    --art-dark: #1a1a1a;
    --art-light: #dcdcdc;
  }
  * { box-sizing: border-box; margin: 0; padding: 0; }
  html, body { width: 1200px; height: 960px; overflow: hidden; }
  body {
    background: var(--backdrop);
    position: relative;
    font-family: "Roboto", Arial, sans-serif;
  }
  .card {
    position: absolute;
    width: 600px;
    height: 343px;
    background: var(--paper-soft);
    overflow: hidden;
  }
  .card-front { left: 314px; top: 113px; }
  .card-back { left: 311px; top: 472px; }

  .front-shape { position: absolute; inset: 0; }

  .holder { position: absolute; left: 43px; top: 54px; color: var(--paper); }
  .holder-name { font-size: 22px; font-weight: 500; letter-spacing: 0.3px; line-height: 1.1; }
  .holder-role { font-size: 14px; margin-top: 3px; }

  .address {
    position: absolute; left: 43px; top: 178px;
    color: var(--paper); font-size: 14px; line-height: 19px; font-style: normal;
  }
  .contact-list {
    position: absolute; left: 43px; top: 226px;
    list-style: none; color: var(--paper); font-size: 14px;
  }
  .contact-list li { display: flex; align-items: center; height: 19px; }
  .contact-icon { width: 12px; height: 12px; margin-right: 10px; fill: var(--paper); }

  .brand-mark {
    position: absolute; left: 335px; top: 150px; width: 220px;
    text-align: center; color: var(--ink);
    font-family: "Roboto Condensed", Arial, sans-serif;
    font-weight: 700; font-size: 26px; line-height: 1.1; text-transform: uppercase;
  }

  .vehicle-art {
    position: absolute; left: 112px; top: 88px; width: 384px; height: 140px;
    background: linear-gradient(180deg, var(--art-light) 0%, var(--art-dark) 60%, var(--art-light) 100%);
    border-radius: 40px 40px 6px 6px;
  }
  .slogan {
    position: absolute; left: 0; right: 0; top: 272px;
    text-align: center; font-weight: 700; font-size: 16px; letter-spacing: 0.4px; color: var(--ink);
  }
  .slogan-rule {
    position: absolute; left: 137px; top: 293px; width: 325px; height: 1.5px; background: var(--ink);
  }
  .services {
    position: absolute; left: 0; right: 0; top: 298px;
    text-align: center; font-family: "Roboto Condensed", Arial, sans-serif;
    font-weight: 700; font-size: 12.5px; color: var(--ink);
  }
</style>
</head>
<body>

<section class="card card-front" aria-label="Business card front">
  <svg class="front-shape" width="600" height="343" viewBox="0 0 600 343" aria-hidden="true">
    <rect width="600" height="343" fill="var(--ink)"/>
    <circle cx="505" cy="171" r="262" fill="none" stroke="var(--paper)" stroke-width="3"/>
    <circle cx="505" cy="171" r="250" fill="var(--paper-soft)"/>
  </svg>

  <div class="holder">
    <div class="holder-name">DALE FERRIS</div>
    <div class="holder-role">CEO/FOUNDER</div>
  </div>

  <address class="address">3847 E Larkin Ave<br>Spokane WA 99214</address>

  <ul class="contact-list">
    <li><svg class="contact-icon" viewBox="0 0 12 12"><path d="M2.5 0.5 L4.5 0.5 L5.2 3.2 L3.8 4.4 Q5 7 7.6 8.2 L8.8 6.8 L11.5 7.5 L11.5 9.5 Q11.5 11.5 9.5 11.5 Q0.5 11 0.5 2.5 Q0.5 0.5 2.5 0.5Z"/></svg>208.417.6352</li>
    <li><svg class="contact-icon" viewBox="0 0 12 12"><path d="M3 0h6a1 1 0 0 1 1 1v10a1 1 0 0 1-1 1H3a1 1 0 0 1-1-1V1a1 1 0 0 1 1-1zM3.2 1.5v8h5.6v-8zM6 10.2a.6.6 0 1 0 0 1.2.6.6 0 0 0 0-1.2z"/></svg>471 529 0836</li>
    <li><svg class="contact-icon" viewBox="0 0 12 12"><path d="M0.5 2.5h11v7h-11z M0.5 2.5 L6 6.8 L11.5 2.5" fill="var(--paper)" stroke="var(--ink)" stroke-width="0.8"/></svg>BrisksPolish@mailvexo.com</li>
    <li><svg class="contact-icon" viewBox="0 0 12 12"><circle cx="6" cy="6" r="5.5"/><path d="M6 .5v11M.5 6h11M6 .5q-3 5.5 0 11M6 .5q3 5.5 0 11" fill="none" stroke="var(--ink)" stroke-width="0.7"/></svg>www.briskspolishworks.com</li>
  </ul>

  <div class="brand-mark">Brisk's<br>Polish Works</div>
</section>

<section class="card card-back" aria-label="Business card back">
  <div class="vehicle-art" role="img" aria-label="Black and white illustration of a classic hot rod in side profile"></div>
  <p class="slogan">WE TAKE PRIDE IN YOUR RIDE</p>
  <div class="slogan-rule" aria-hidden="true"></div>
  <p class="services">we offer services on anything including cars, trucks, motorcycles &amp; RVs</p>
</section>

</body>
</html>
```